TalkHarbor - Language Coaching Services

Sleek, innovative, trendy design for Language Coaching business.

TalkHarbor is a new UK based company that provides Language Coaching services. We offer highly personalized on-line and face to face language courses. We also impart learning techniques workshops based on the latest neuroscience research for second-language acquisition.

Target Market(s)

See attached info

Industry/Entity Type

Consulting

Contact Information for Business Card

TalkHarbor
DaniaKV@talkharbor.co.uk
TalkHarbor.co.uk
London, UK

Font styles to use
Sans Serif

```html
<!DOCTYPE html>
<html lang="en">
<head>
<meta charset="utf-8">
<title>TalkHarbor – Business Card</title>
<link rel="stylesheet" href="https://fonts.googleapis.com/css2?family=Open+Sans:wght@400;600;700&display=swap">
<style>
  :root {
    --page-bg: #ece9e4;
    --card-dark: #2b2a2b;
    --card-light: #ffffff;
    --brand-blue: #1a93c9;
    --ink: #1f1f1f;
    --ink-light: #f2f2f2;
  }
  * { margin: 0; padding: 0; box-sizing: border-box; }
  html, body {
    width: 1200px; height: 900px; overflow: hidden;
    background: var(--page-bg);
    font-family: "Open Sans", Arial, sans-serif;
  }
  .stage {
    position: relative; width: 1200px; height: 900px;
  }
  .card {
    position: absolute; left: 320px; width: 560px; height: 320px;
    border-radius: 22px; overflow: hidden;
    box-shadow: 0 10px 28px rgba(0,0,0,0.22);
  }
  /* Back side */
  .card-back {
    top: 105px; background: var(--card-dark);
    display: flex; flex-direction: column; align-items: center; justify-content: center;
  }
  .back-mark {
    width: 92px; height: 92px; border-radius: 50%;
    border: 6px solid var(--brand-blue); margin-bottom: 18px;
  }
  .back-name {
    color: var(--brand-blue); font-weight: 600; font-size: 46px;
    letter-spacing: 2px; text-transform: uppercase; line-height: 1;
  }
  .back-web {
    margin-top: 28px; color: var(--ink-light); font-size: 15px; font-weight: 600; letter-spacing: 0.5px;
  }
  /* Front side */
  .card-front {
    top: 475px; background: var(--card-light);
  }
  .front-edge {
    position: absolute; left: 0; right: 0; bottom: 0; height: 14px; background: var(--brand-blue);
  }
  .front-brand {
    position: absolute; left: 34px; top: 96px;
    display: flex; align-items: center; gap: 12px;
  }
  .front-mark {
    width: 56px; height: 56px; border-radius: 50%; border: 4px solid var(--brand-blue);
  }
  .front-name {
    color: var(--brand-blue); font-weight: 600; font-size: 24px; letter-spacing: 1px; text-transform: uppercase;
  }
  .divider {
    position: absolute; left: 300px; top: 78px; width: 2px; height: 96px; background: var(--brand-blue);
  }
  .contact {
    position: absolute; left: 326px; top: 80px; list-style: none;
  }
  .contact-title {
    color: var(--brand-blue); font-weight: 700; font-size: 18px; margin-bottom: 6px;
  }
  .contact-item {
    display: flex; align-items: center; gap: 12px;
    font-size: 15px; color: var(--ink); letter-spacing: 0.4px; line-height: 24px;
  }
  .contact-item svg { width: 16px; height: 16px; flex: none; fill: var(--brand-blue); }
  .address {
    position: absolute; left: 0; right: 0; top: 246px; text-align: center;
    font-size: 15px; color: var(--ink); font-weight: 600; letter-spacing: 0.4px;
  }
</style>
</head>
<body>
<main class="stage">
  <section class="card card-back">
    <div class="back-mark"></div>
    <div class="back-name">TalkHarbor</div>
    <div class="back-web">www.talkharbor.co.uk</div>
  </section>

  <section class="card card-front">
    <div class="front-brand">
      <div class="front-mark"></div>
      <div class="front-name">TalkHarbor</div>
    </div>
    <div class="divider"></div>
    <ul class="contact">
      <li class="contact-title">TalkHarbor</li>
      <li class="contact-item">
        <svg viewBox="0 0 24 24" aria-hidden="true"><path d="M6.6 10.8a15.1 15.1 0 0 0 6.6 6.6l2.2-2.2c.3-.3.7-.4 1-.2 1.1.4 2.3.6 3.6.6.6 0 1 .4 1 1V20c0 .6-.4 1-1 1A17 17 0 0 1 3 4c0-.6.4-1 1-1h3.5c.6 0 1 .4 1 1 0 1.3.2 2.5.6 3.6.1.3 0 .7-.2 1z"/></svg>
        +44 1632 960518
      </li>
      <li class="contact-item">
        <svg viewBox="0 0 24 24" aria-hidden="true"><path d="M2 5h20v14H2zm2 2v.4l8 5.2 8-5.2V7zm0 2.8V17h16V9.8l-8 5.2z"/></svg>
        DaniaKV@talkharbor.co.uk
      </li>
      <li class="contact-item">
        <svg viewBox="0 0 24 24" aria-hidden="true"><path d="M12 2a10 10 0 1 0 0 20 10 10 0 0 0 0-20zm6.9 9h-3a15 15 0 0 0-1.3-5.6A8 8 0 0 1 18.9 11zM12 4.1c.9 1.2 1.8 3.6 1.9 6.9h-3.8c.1-3.3 1-5.7 1.9-6.9zM9.4 5.4A15 15 0 0 0 8.1 11h-3a8 8 0 0 1 4.3-5.6zM5.1 13h3a15 15 0 0 0 1.3 5.6A8 8 0 0 1 5.1 13zm6.9 6.9c-.9-1.2-1.8-3.6-1.9-6.9h3.8c-.1 3.3-1 5.7-1.9 6.9zm2.6-1.3a15 15 0 0 0 1.3-5.6h3a8 8 0 0 1-4.3 5.6z"/></svg>
        www.talkharbor.co.uk
      </li>
    </ul>
    <p class="address">27 Harbour Lane, SE1 4QR, London, UK</p>
    <div class="front-edge"></div>
  </section>
</main>
</body>
</html>
```